MALT CALEDON/BRACKENRIDGE DISTILLERY

DOUBLE SIDED BUSINESS CARD ONE SIDE FOR WWW.MALTCALEDON.ORG AND ONE SIDE FOR BRACKENRIDGE DISTILLERY ARTWORK FOR WEBSITE IS ATTACHED

1)
GORDON PRITCHARD CEO
MALT CALEDON
Office 1 Harbourgate House
14 Fernbrook Place
Glasgow
Scotland, G5 2QT
W:WWW.MALTCALEDON.ORG
E:GORDON@MALTCALEDON.ORG
T:+44 7491 355018

2)
GORDON PRITCHARD CEO
BRACKENRIDGE DISTILLERY
Building 418, Hangarpark Oosterhof,
3e Brinkweg, Katwijk, 2226KM

W: WWW.brackenridgedistillery.nl
E: GORDON@brackenridgedistillery.nl
T:+44 7491 355018

1)
Marit Steenbergen DIRECTOR
MALT CALEDON
Office 1 Harbourgate House
14 Fernbrook Place
Glasgow
Scotland, G5 2QT
W:WWW.MALTCALEDON.ORG
E:Marit@MALTCALEDON.ORG
T:+31 6 58193047

2)
MARIT STEENBERGEN DIRECTOR
BRACKENRIDGE DISTILLERY

E: marit@brackenridgedistillery.nl
T:+31 6 58193047

```html
<!DOCTYPE html>
<html lang="en">
<head>
<meta charset="utf-8">
<title>Malt Caledon / Brackenridge Distillery business cards</title>
<link rel="stylesheet" href="https://fonts.googleapis.com/css2?family=Marcellus&family=Montserrat:wght@400;500;600&display=swap">
<style>
  :root{
    --bg:#ebebeb;
    --paper:#ffffff;
    --gold:#b8913a;
    --gold-soft:#c9a03d;
    --gold-deep:#a9832c;
    --ink:#2a2a2a;
    --grey:#5e5e5e;
  }
  *{box-sizing:border-box;margin:0;padding:0}
  html,body{width:1200px;height:900px;overflow:hidden}
  body{background:var(--bg);font-family:"Montserrat",sans-serif;color:var(--ink);position:relative}

  .card{position:absolute;width:436px;height:262px;overflow:hidden}
  .card--front{background:var(--paper)}
  .card--back{background:var(--gold-soft);display:flex;align-items:center;justify-content:center}

  .card--malt-front{left:136px;top:124px}
  .card--malt-back{left:634px;top:124px}
  .card--brack-front{left:136px;top:498px}
  .card--brack-back{left:634px;top:498px}

  .brand{position:absolute;left:30px;display:flex;align-items:center;gap:10px}
  .brand__mark{width:14px;height:14px;border-radius:50%;background:var(--gold)}
  .brand__name{white-space:nowrap}
  .brand--malt{top:112px}
  .brand--malt .brand__name{font-family:"Marcellus",serif;font-size:26px;color:var(--gold);letter-spacing:1px}
  .brand--brack{top:48px}
  .brand--brack .brand__mark{border-radius:0;background:var(--ink);width:12px;height:12px}
  .brand--brack .brand__name{font-family:"Montserrat",sans-serif;font-weight:600;font-size:19px;color:var(--ink);letter-spacing:.5px}

  .holder{position:absolute;right:22px;text-align:right}
  .holder__name{color:var(--gold);white-space:nowrap}
  .holder__role{font-size:10px;color:var(--ink);margin-top:3px}
  .card--malt-front .holder{top:152px}
  .card--malt-front .holder__name{font-family:"Marcellus",serif;font-size:20px}
  .card--brack-front .holder{top:158px}
  .card--brack-front .holder__name{font-family:"Montserrat",sans-serif;font-weight:500;font-size:15px}

  .rule{position:absolute;left:30px;right:22px;height:1px;background:var(--gold)}
  .card--malt-front .rule{top:196px}
  .card--brack-front .rule{top:198px}

  .contacts{position:absolute;left:30px;list-style:none;font-size:9.6px;line-height:13px}
  .contacts li{display:flex;align-items:center;gap:6px}
  .contacts svg{width:9px;height:9px;flex:none;fill:var(--gold)}
  .card--malt-front .contacts{top:205px}
  .card--brack-front .contacts{top:208px}

  .address{position:absolute;right:22px;text-align:right;font-size:9.6px;line-height:12.5px;font-style:normal}
  .card--malt-front .address{top:209px}
  .card--brack-front .address{top:218px}

  .band{position:absolute;left:0;right:0;bottom:0;height:8px;background:var(--grey)}
  .band__gold{position:absolute;left:0;top:0;bottom:0;width:64%;background:var(--gold-soft);clip-path:polygon(0 0,100% 0,calc(100% - 8px) 100%,0 100%)}
  .band__cut{position:absolute;top:0;bottom:0;left:calc(64% - 4px);width:8px;background:var(--paper);clip-path:polygon(8px 0,100% 0,calc(100% - 8px) 100%,0 100%);transform:translateX(3px)}

  .back-brand{display:flex;align-items:center;gap:12px}
  .back-brand__mark{width:18px;height:18px;border-radius:50%;background:var(--gold-deep)}
  .back-brand__name{color:var(--gold-deep);white-space:nowrap}
  .card--malt-back .back-brand__name{font-family:"Marcellus",serif;font-size:38px;letter-spacing:1px}
  .card--brack-back .back-brand__mark{border-radius:0;width:16px;height:16px}
  .card--brack-back .back-brand__name{font-family:"Montserrat",sans-serif;font-weight:600;font-size:26px}
</style>
</head>
<body>

<svg width="0" height="0" style="position:absolute" aria-hidden="true">
  <symbol id="icon-phone" viewBox="0 0 10 10"><path d="M1 3.2C1 2 2.5 1 5 1s4 1 4 2.2V4H7V3H3v1H1z M2 5h6l1 4H1z"/></symbol>
  <symbol id="icon-mail" viewBox="0 0 10 10"><path d="M0 2h10v1L5 5.5 0 3z M0 4.2l5 2.5 5-2.5V8H0z"/></symbol>
  <symbol id="icon-web" viewBox="0 0 10 10"><path d="M5 0a5 5 0 1 0 0 10A5 5 0 0 0 5 0zm0 1.2a3.8 3.8 0 0 1 3.7 3H6.3L5 2.5 3.6 4.2H1.3A3.8 3.8 0 0 1 5 1.2zM1.3 5.8h2.3L5 7.5l1.3-1.7h2.4A3.8 3.8 0 0 1 1.3 5.8z"/></symbol>
</svg>

<section class="card card--front card--malt-front">
  <div class="brand brand--malt"><span class="brand__mark"></span><span class="brand__name">MALT CALEDON</span></div>
  <div class="holder"><p class="holder__name">Marit Steenbergen</p><p class="holder__role">Director</p></div>
  <div class="rule"></div>
  <ul class="contacts">
    <li><svg><use href="#icon-phone"/></svg>+31 6 58193047</li>
    <li><svg><use href="#icon-mail"/></svg>marit@maltcaledon.org</li>
    <li><svg><use href="#icon-web"/></svg>www.maltcaledon.org</li>
  </ul>
  <address class="address">Harbourgate House<br>14 Fernbrook Place<br>Glasgow, Scotland, G5 2QT</address>
  <div class="band"><span class="band__gold"></span><span class="band__cut"></span></div>
</section>

<section class="card card--back card--malt-back">
  <div class="back-brand"><span class="back-brand__mark"></span><span class="back-brand__name">MALT CALEDON</span></div>
</section>

<section class="card card--front card--brack-front">
  <div class="brand brand--brack"><span class="brand__mark"></span><span class="brand__name">BRACKENRIDGE DISTILLERY</span></div>
  <div class="holder"><p class="holder__name">MARIT STEENBERGEN</p><p class="holder__role">Director</p></div>
  <div class="rule"></div>
  <ul class="contacts">
    <li><svg><use href="#icon-phone"/></svg>+31 6 58193047</li>
    <li><svg><use href="#icon-mail"/></svg>marit@brackenridgedistillery.nl</li>
    <li><svg><use href="#icon-web"/></svg>www.brackenridgedistillery.nl</li>
  </ul>
  <address class="address">Building 418, Hangarpark Oosterhof<br>3e Brinkweg, Katwijk, 2226KM</address>
  <div class="band"><span class="band__gold"></span><span class="band__cut"></span></div>
</section>

<section class="card card--back card--brack-back">
  <div class="back-brand"><span class="back-brand__mark"></span><span class="back-brand__name">BRACKENRIDGE DISTILLERY</span></div>
</section>

</body>
</html>
```